Heron Loan Partners Business Card

We need a business card design for our mortgage servicing company. In addition to servicing the loans of homeowners, we help homeowners with purchasing their homes and any mortgage refinancing. We would like to see designs that use the colors in the logo attached below (gold-ish yellow and navy blue), and any other design you deem fit! The design should communicate a simpler life with smart mortgages provided by Heron.

```html
<!DOCTYPE html>
<html lang="en">
<head>
<meta charset="utf-8">
<title>Heron Loan Partners Business Card</title>
<link rel="stylesheet" href="https://fonts.googleapis.com/css2?family=Montserrat:wght@500;700&display=swap">
<style>
  :root {
    --navy: #27215a;
    --gold: #e4b43a;
    --white: #ffffff;
    --stage: #e9e8ee;
    --soft-white: #e7e6f0;
  }
  * { margin: 0; padding: 0; box-sizing: border-box; }
  html, body { width: 1200px; height: 799px; overflow: hidden; }
  body {
    background: var(--stage);
    font-family: "Montserrat", Arial, sans-serif;
    display: flex;
    align-items: center;
    justify-content: center;
    gap: 48px;
  }
  .card {
    position: relative;
    width: 540px;
    height: 309px;
    border-radius: 18px;
    overflow: hidden;
    box-shadow: 0 6px 18px rgba(20, 18, 50, 0.18);
  }
  .card-front {
    background: var(--white);
    display: flex;
    align-items: center;
    justify-content: center;
  }
  .brand-name {
    font-weight: 700;
    font-size: 38px;
    letter-spacing: 0.5px;
    color: var(--gold);
    display: flex;
    align-items: center;
    gap: 12px;
  }
  .brand-dot {
    width: 14px;
    height: 14px;
    border-radius: 50%;
    background: var(--navy);
  }
  .card-back { background: var(--navy); }
  .card-back .brand-name {
    position: absolute;
    left: 70px;
    top: 62px;
    font-size: 32px;
    color: var(--soft-white);
  }
  .card-back .brand-dot { background: var(--gold); }
  .holder {
    position: absolute;
    left: 44px;
    bottom: 44px;
  }
  .holder-name {
    font-weight: 700;
    font-size: 21px;
    color: var(--gold);
    letter-spacing: 0.5px;
  }
  .holder-title {
    font-weight: 500;
    font-size: 14px;
    color: var(--white);
    margin-top: 4px;
  }
  .contact {
    position: absolute;
    right: 32px;
    top: 150px;
    list-style: none;
  }
  .contact li {
    display: flex;
    align-items: center;
    gap: 9px;
    font-size: 11.5px;
    font-weight: 500;
    color: var(--white);
    margin-bottom: 7px;
  }
  .contact li:first-child { font-size: 14px; }
  .contact svg { width: 11px; height: 11px; flex: none; }
  .accent-bar {
    position: absolute;
    right: 0;
    bottom: 30px;
    width: 190px;
    height: 8px;
    background: var(--gold);
  }
</style>
</head>
<body>
  <section class="card card-front" aria-label="Card front">
    <div class="brand-name"><span class="brand-dot"></span>Heron Loan Partners</div>
  </section>

  <section class="card card-back" aria-label="Card back">
    <div class="brand-name"><span class="brand-dot"></span>Heron Loan Partners</div>

    <ul class="contact">
      <li>
        <svg viewBox="0 0 12 12" aria-hidden="true"><path d="M2.5 1h2l1 2.5-1.3 1a6 6 0 0 0 3.3 3.3l1-1.3L11 7.5v2A1.5 1.5 0 0 1 9.5 11 8.5 8.5 0 0 1 1 2.5 1.5 1.5 0 0 1 2.5 1z" fill="var(--gold)"/></svg>
        (555) 210-4830
      </li>
      <li>
        <svg viewBox="0 0 12 12" aria-hidden="true"><rect x="1" y="2.5" width="10" height="7" rx="1" fill="var(--gold)"/><path d="M1.5 3l4.5 3.5L10.5 3" stroke="var(--navy)" stroke-width="1" fill="none"/></svg>
        info@heronloanpartners.com
      </li>
      <li>
        <svg viewBox="0 0 12 12" aria-hidden="true"><circle cx="6" cy="6" r="5" fill="var(--gold)"/><path d="M1 6h10M6 1c2 2 2 8 0 10M6 1c-2 2-2 8 0 10" stroke="var(--navy)" stroke-width="0.8" fill="none"/></svg>
        heronloanpartners.com
      </li>
    </ul>

    <div class="holder">
      <p class="holder-name">DANIEL BROOKS</p>
      <p class="holder-title">Founder &amp; CEO</p>
    </div>

    <div class="accent-bar"></div>
  </section>
</body>
</html>
```